Restyle corporate identity (+ logo) for a road construction company

We need a new logo and stationary design for our company VARNOK path. VARNOK path® increases the road base strength, while reducing major costs and time of road construction. Attached some examples of the current design.

Our wishes for the new logo:
- Business look
- Style sheet
- Modern

More information: www.varnokpath.example
Updates

Target Market(s)

Government

Industry/Entity Type

Construction

Requirements
Must have
• Logo (with road sign) + text

```html
<!DOCTYPE html>
<html lang="en">
<head>
<meta charset="utf-8">
<title>VARNOK path – Stationery</title>
<link rel="stylesheet" href="https://fonts.googleapis.com/css2?family=Source+Sans+3:wght@400;600&display=swap">
<style>
  :root {
    --bg: #ece9e4;
    --paper: #f1f1f1;
    --paper-shade: #e6e6e6;
    --green: #9bc224;
    --grey: #9a9a9a;
    --grey-light: #d6d6d6;
    --brand-grey: #8c8c8c;
    --ink: #2b2b2b;
    --white: #ffffff;
  }
  * { box-sizing: border-box; margin: 0; padding: 0; }
  html, body { width: 1200px; height: 809px; overflow: hidden; }
  body {
    position: relative;
    background: var(--bg);
    font-family: "Source Sans 3", "Helvetica Neue", Arial, sans-serif;
    color: var(--ink);
  }

  /* ---------- Letterhead ---------- */
  .letterhead {
    position: absolute; left: 54px; top: 52px; width: 496px; height: 702px;
    background: linear-gradient(135deg, var(--paper) 0%, var(--paper-shade) 100%);
    box-shadow: 0 2px 8px rgba(0,0,0,.18);
    overflow: hidden;
  }
  .brand {
    position: absolute; display: flex; align-items: center; gap: 14px;
  }
  .brand-dot {
    width: 40px; height: 40px; border-radius: 50%; background: var(--green);
  }
  .brand-name {
    font-weight: 600; font-size: 27px; color: var(--brand-grey); letter-spacing: 0.5px;
  }
  .letterhead .brand { left: 38px; top: 62px; }

  .letter {
    position: absolute; left: 37px; top: 221px; width: 434px;
    font-size: 8.2px; line-height: 10.9px;
  }
  .letter .salutation { margin-bottom: 22px; }
  .letter p { margin-bottom: 10.5px; text-align: left; }
  .letter .signoff { margin-top: 20px; }
  .signature {
    width: 72px; height: 30px; margin-top: 10px;
    background: linear-gradient(90deg, rgba(40,70,160,.25), rgba(40,70,160,.08));
    border-radius: 4px;
  }

  .footer-band { position: absolute; left: 0; bottom: 0; width: 496px; height: 702px; }

  .contacts {
    position: absolute; right: 30px; top: 630px; text-align: right;
    color: var(--white); font-size: 8.6px; line-height: 14.5px;
  }
  .contacts li { list-style: none; display: flex; justify-content: flex-end; align-items: center; gap: 5px; }
  .contacts svg { width: 9px; height: 9px; }
  .contacts .address { margin-top: 2px; }

  /* ---------- Envelope ---------- */
  .envelope { position: absolute; left: 568px; top: 394px; width: 584px; height: 360px; }
  .envelope-flap { position: absolute; left: 0; top: 0; width: 584px; height: 99px; }
  .flap-circle {
    position: absolute; left: 260px; top: 20px; width: 64px; height: 64px;
    border: 3px solid var(--white); border-radius: 50%;
  }
  .envelope-body {
    position: absolute; left: 0; top: 98px; width: 584px; height: 262px;
    background: linear-gradient(135deg, var(--paper) 0%, var(--paper-shade) 100%);
    box-shadow: 0 2px 8px rgba(0,0,0,.18);
    overflow: hidden;
  }
  .envelope-body .brand { left: 26px; top: 20px; }
  .envelope-body .brand-dot { width: 42px; height: 42px; }
  .envelope-address {
    position: absolute; left: 26px; top: 69px; font-size: 8.8px; line-height: 12px; color: #444;
  }
  .envelope-body .footer-band { width: 584px; height: 262px; }
</style>
</head>
<body>

<section class="letterhead" aria-label="Letterhead">
  <div class="brand">
    <span class="brand-dot"></span>
    <span class="brand-name">VARNOK path</span>
  </div>

  <article class="letter">
    <p class="salutation">Dear Mr. Halberg,</p>
    <p>Lorem ipsum dolor sit amet, consectetur adipiscing elit. Donec orci purus, luctus vitae dignissim eu, iaculis sed purus. Vivamus faucibus, ipsum nec aliquet viverra, leo mauris condimentum ligula, sit amet sagittis enim ligula quis arcu. Nam egestas tortor id nisi porttitor mattis. In tortor ante, ultricies in suscipit a, tempus non massa. Vivamus et auctor mi.</p>
    <p>Fusce vel massa nulla. Phasellus nec eros mauris, et scelerisque orci. Donec malesuada orci vitae nulla accumsan porta a id massa. Quisque accumsan iaculis magna sit amet fringilla. Maecenas consequat, magna eget tincidunt semper, odio nibh rutrum mi, id feugiat ante nisi eu risus. Vestibulum nunc orci, rhoncus a placerat in, ultricies in mi. Cras mattis varius eros, vel fringilla nisi suscipit eget.</p>
    <p>Quisque scelerisque sagittis nulla at porttitor. Mauris a justo et tellus interdum tristique. Sed id augue vitae urna euismod commodo aliquet a quam. Pellentesque arcu velit, cursus et malesuada ut, consequat et diam. Nullam erat sem, rhoncus id ullamcorper vitae, rhoncus et arcu. In ultricies ultricies nulla, ut rutrum nisi iaculis at. Donec eu magna a metus ornare faucibus.</p>
    <p>Fusce aliquet faucibus ultricies. Morbi semper, est id tincidunt gravida, sem arcu adipiscing lacus, ac bibendum nulla leo eu purus. Quisque nec diam sed risus consectetur a ccumsan quis quis nibh. Vestibulum id purus lorem.</p>
    <p class="signoff">Mara Lindqvist<br>Co-Founder &amp; CEO</p>
    <div class="signature" role="img" aria-label="Handwritten signature of Mara Lindqvist"></div>
  </article>

  <svg class="footer-band" viewBox="0 0 496 702" aria-hidden="true">
    <polygon points="0,679 496,577 496,580 0,685" fill="var(--green)"/>
    <polygon points="0,685 496,580 496,583 0,691" fill="var(--grey-light)"/>
    <polygon points="0,691 496,583 496,587 0,698" fill="var(--grey)"/>
    <polygon points="0,698 496,587 496,589 0,702" fill="var(--white)"/>
    <polygon points="0,702 496,589 496,702" fill="var(--green)"/>
  </svg>

  <ul class="contacts">
    <li>+31 20 555 01 47
      <svg viewBox="0 0 10 10"><path d="M1 4 Q5 0 9 4 L8 5 L6 4 L4 4 L2 5 Z M2 5 H8 V9 H2 Z" fill="var(--white)"/></svg></li>
    <li>office@varnokpath.example
      <svg viewBox="0 0 10 10"><rect x="0.5" y="2" width="9" height="6.5" fill="var(--white)"/><path d="M0.5 2 L5 5.5 L9.5 2" stroke="var(--green)" fill="none" stroke-width="0.8"/></svg></li>
    <li>www.varnokpath.example
      <svg viewBox="0 0 10 10"><circle cx="5" cy="5" r="4.3" fill="none" stroke="var(--white)" stroke-width="0.9"/><path d="M0.7 5 H9.3 M5 0.7 V9.3" stroke="var(--white)" stroke-width="0.7"/></svg></li>
    <li class="address">Kelder Brinkstraat 58, 4812 KT Verlaan, The Netherlands</li>
  </ul>
</section>

<section class="envelope" aria-label="Envelope">
  <svg class="envelope-flap" viewBox="0 0 584 99" aria-hidden="true">
    <path d="M0 99 L12 36 Q20 0 60 0 H524 Q564 0 572 36 L584 99 Z" fill="var(--green)"/>
  </svg>
  <div class="flap-circle"></div>

  <div class="envelope-body">
    <div class="brand">
      <span class="brand-dot"></span>
      <span class="brand-name">VARNOK path</span>
    </div>
    <p class="envelope-address">Kelder Brinkstraat 58<br>4812 KT Verlaan, The Netherlands</p>

    <svg class="footer-band" viewBox="0 0 584 262" aria-hidden="true">
      <polygon points="0,239 584,137 584,140 0,245" fill="var(--green)"/>
      <polygon points="0,245 584,140 584,143 0,251" fill="var(--grey-light)"/>
      <polygon points="0,251 584,143 584,147 0,258" fill="var(--grey)"/>
      <polygon points="0,258 584,147 584,149 0,262" fill="var(--white)"/>
      <polygon points="0,262 584,149 584,262" fill="var(--green)"/>
    </svg>
  </div>
</section>

</body>
</html>
```